Fitness Centre/Personal Trainer Business Card

We need a business card design for a company based in Singapore called 'Vigor Ledger'.

We are a team of Personal Trainers and we are planning to open our new training facility.

This design will also be printed/painted on the walls in our gym.

We are a new breed of personal trainers who take fitness seriously and holistically. We do not merely train our clients to be big and muscular.

We believe in wholeness. In our opinion, fitness should include: strength, speed, flexibility, mobility, stamina & agility. These are what we train for. Of course, nutrition/diet is key.

We use fitness tools such as kettlebells, QVL, Pylometric boxes, battling ropes, clubbells, medicine balls, bulgarian bags etc - functional and non-bulky tools.

I currently have a Facebook page 'Vigor Ledger SG' which shows a logo of a kettlebell. But my business focus has since changed.

Services provided:
- Kettlebell Sport Preparation
- Calisthenics Training
- Corrective Exercises
- Sports Strength & Conditioning
- 28 days Weight Loss Program
- Myofascial Rehab Therapy
- Sports/Thai Massage

Main colors for the design should be BLACK & YELLOW. We envision a design which is able to protray the holistic view we take on fitness. Also it should somewhat appeal to the ladies and not intimidate them.

Target Market(s)

People between 18-35 years old. Students and working class alike.

Industry/Entity Type

Training

Requirements
Must have
• Name: Marcus Obadiah Lim
Fitness Coach
Corrective Exercise Specialist
M: +65 9437 2065
E: marcus@sgvigorledger-example.com

Double-sided please.
Nice to have
• "What is your vigor ledger?"

```html
<!DOCTYPE html>
<html lang="en">
<head>
<meta charset="utf-8">
<title>Vigor Ledger Business Card</title>
<link rel="stylesheet" href="https://fonts.googleapis.com/css2?family=Source+Sans+3:wght@400;600;700&display=swap">
<style>
  :root {
    --bg: #e9e7e3;
    --card-top: #2e2e2e;
    --card-bottom: #1b1b1b;
    --card-black: #050505;
    --yellow: #f7d21c;
    --yellow-text: #f5c81a;
    --white: #ffffff;
    --soft-white: #e8e8e8;
    --bar-grey: #5b5b5b;
  }
  * { box-sizing: border-box; margin: 0; padding: 0; }
  html, body {
    width: 1200px; height: 722px; overflow: hidden;
    background: var(--bg);
    font-family: "Source Sans 3", "Myriad Pro", sans-serif;
  }
  .canvas { position: relative; width: 1200px; height: 722px; }

  .card {
    position: absolute; width: 516px; height: 294px;
    border-radius: 12px; overflow: hidden;
    background: linear-gradient(135deg, var(--card-top), var(--card-bottom));
    box-shadow: 0 4px 14px rgba(0,0,0,.25);
  }
  .card--front { left: 366px; top: 29px; }
  .card--back-list { left: 94px; top: 375px; }
  .card--back-wide { left: 639px; top: 382px; background: var(--card-black); }

  /* brand lockup */
  .brand {
    position: absolute; display: flex; align-items: center; gap: 10px;
    color: var(--yellow); font-weight: 700; line-height: .95;
    font-size: 30px;
  }
  .brand__dot { width: 16px; height: 16px; border-radius: 50%; background: var(--yellow); flex: none; }
  .card--front .brand { left: 62px; top: 100px; }
  .card--back-list .brand { left: 56px; top: 110px; }

  /* front */
  .divider {
    position: absolute; left: 276px; top: 42px; width: 2px; height: 160px;
    background: linear-gradient(to bottom, transparent, #cfcfcf 50%, transparent);
  }
  .contact { position: absolute; left: 298px; top: 56px; color: var(--soft-white); }
  .contact__name { color: var(--yellow-text); font-weight: 700; font-size: 18px; line-height: 22px; }
  .contact__role { font-size: 13px; line-height: 18px; }
  .contact__list { list-style: none; margin-top: 20px; font-size: 13px; line-height: 19px; }
  .contact__list li { display: flex; align-items: center; gap: 6px; }
  .contact__list svg { width: 9px; height: 9px; fill: var(--yellow); flex: none; }

  .bar { position: absolute; top: 238px; height: 10px; }
  .bar--yellow { left: 0; width: 274px; background: var(--yellow); }
  .bar--grey { left: 281px; right: 0; background: var(--bar-grey); }

  .slogan {
    position: absolute; left: 0; right: 0; text-align: center;
    color: var(--yellow-text); font-weight: 700; font-size: 16.5px; letter-spacing: 1.2px;
  }
  .card--front .slogan { top: 262px; }
  .card--back-list .slogan { top: 262px; }
  .card--back-wide .slogan { top: 254px; }

  /* services */
  .services__title { color: var(--yellow-text); font-weight: 700; font-size: 19px; }
  .services__list { list-style: none; color: var(--soft-white); font-size: 15px; }
  .services__list li::before { content: "\2022"; margin-right: 4px; color: var(--white); }

  .card--back-list .services { position: absolute; left: 268px; top: 26px; }
  .card--back-list .services__title { margin-bottom: 14px; }
  .card--back-list .services__list li { line-height: 26.5px; }

  .card--back-wide .services { position: absolute; left: 0; right: 0; top: 76px; text-align: center; }
  .card--back-wide .services__title { margin-bottom: 14px; }
  .card--back-wide .services__list { font-size: 17px; line-height: 32px; }
  .card--back-wide .services__list li { display: inline; margin: 0 3px; }
  .card--back-wide .services__list li::before { margin-right: 3px; }
</style>
</head>
<body>
<div class="canvas">

  <section class="card card--front" aria-label="Business card front">
    <div class="brand"><span class="brand__dot"></span><span>Vigor<br>Ledger</span></div>
    <div class="divider"></div>
    <div class="contact">
      <p class="contact__name">Marcus Obadiah Lim</p>
      <p class="contact__role">Fitness Coach</p>
      <p class="contact__role">Corrective Exercise Specialist</p>
      <ul class="contact__list">
        <li><svg viewBox="0 0 10 10"><rect x="2.5" y="0" width="5" height="10" rx="1"/></svg>+65 9437 2065</li>
        <li><svg viewBox="0 0 10 10"><rect x="0" y="2" width="10" height="6"/></svg>marcus@sgvigorledger-example.com</li>
        <li><svg viewBox="0 0 10 10"><circle cx="5" cy="5" r="5"/></svg>www.sgvigorledger-example.com</li>
      </ul>
    </div>
    <div class="bar bar--yellow"></div>
    <div class="bar bar--grey"></div>
    <p class="slogan">WHAT IS YOUR VIGOR LEDGER ?</p>
  </section>

  <section class="card card--back-list" aria-label="Business card back, list layout">
    <div class="brand"><span class="brand__dot"></span><span>Vigor<br>Ledger</span></div>
    <div class="services">
      <h2 class="services__title">Services</h2>
      <ul class="services__list">
        <li>Sports Strength &amp; Conditioning</li>
        <li>Kettlebell Sport Preparation</li>
        <li>28 days Weight Loss Program</li>
        <li>Myofascial Rehab Therapy</li>
        <li>Calisthenics Training</li>
        <li>Corrective Exercises</li>
        <li>Sports/Thai Massage</li>
      </ul>
    </div>
    <p class="slogan">WHAT IS YOUR VIGOR LEDGER ?</p>
  </section>

  <section class="card card--back-wide" aria-label="Business card back, centred layout">
    <div class="services">
      <h2 class="services__title">Services</h2>
      <ul class="services__list">
        <li>Sports Strength &amp; Conditioning</li>
        <li>Sports/Thai Massage</li><br>
        <li>Kettlebell Sport Preparation</li>
        <li>Corrective Exercises</li><br>
        <li>28 days Weight Loss Program</li>
        <li>Calisthenics Training</li><br>
        <li>Myofascial Rehab Therapy</li>
      </ul>
    </div>
    <p class="slogan">WHAT IS YOUR VIGOR LEDGER ?</p>
  </section>

</div>
</body>
</html>
```